KRL Stationery Design Project

Dear Designers,
We need a new stationery design for company to match our new logo.
Designers should provide a design for the following:
1. Business Card: 3.5x2 Inches.
2. Letterhead: A4 size.
3. Envelops: 25x35.5 Cm.
You can keep the Arabic name at the bottom of the logo Or you can use the separate attached Arabic Name.
Please refer to the attached logo guide for design information.
Sample Business Card information:
Name: Tarek Sowan
Position: Operation Manager
Tel: +966 920007164 Ex. 500
Fax: +966 (3)8842617
Mob: +966 (5)00263817
email: tarek@krl-example.com.sa
URL: www.krl-example.com.sa
Address:
Nakheel Heights, Suite 718
Zayed bin Omar Str.
Khobar, 31847
Saudi Arabia
Updates
Dear All,
Please note, we had uploaded our logo along with Arabic writing in Adobe illustrator format (.ai).
Regards,
Karim
Dear All,
A sample data for the business card had been added as per your request.
Regards,
Karim

```html
<!DOCTYPE html>
<html lang="en">
<head>
<meta charset="utf-8">
<title>KRL Business Card</title>
<link href="https://fonts.googleapis.com/css2?family=Source+Sans+3:wght@400;600;700&display=swap" rel="stylesheet">
<style>
  :root {
    --backdrop: #1c1c1c;
    --card: #ffffff;
    --navy: #173a63;
    --ink: #444444;
    --muted: #6b6b6b;
    --rule: #b3b3b3;
    --frame: #9a9a9a;
  }
  * { box-sizing: border-box; margin: 0; padding: 0; }
  html, body { width: 1200px; height: 472px; overflow: hidden; }
  body {
    background: var(--backdrop);
    font-family: "Source Sans 3", Arial, sans-serif;
    position: relative;
  }
  .card {
    position: absolute;
    top: 84px;
    width: 524px;
    height: 299px;
    background: var(--card);
    border-radius: 14px;
    overflow: hidden;
  }
  .card--front { left: 60px; }
  .card--back { left: 604px; }

  .brand {
    position: absolute;
    display: flex;
    align-items: center;
    gap: 12px;
    color: var(--navy);
    font-weight: 700;
    line-height: 1;
  }
  .brand__mark {
    width: 20px;
    height: 20px;
    background: var(--navy);
  }
  .card--front .brand { left: 40px; top: 62px; font-size: 56px; }
  .card--back .brand {
    left: 50%;
    top: 98px;
    transform: translateX(-50%);
    font-size: 60px;
  }

  .holder {
    position: absolute;
    right: 30px;
    top: 190px;
    color: var(--navy);
    font-size: 17px;
    font-weight: 700;
    letter-spacing: -0.2px;
  }
  .holder__title { font-weight: 400; font-size: 14px; color: var(--ink); }

  .divider {
    position: absolute;
    left: 0;
    right: 0;
    top: 213px;
    height: 2px;
    background: var(--rule);
  }

  .contacts {
    position: absolute;
    left: 40px;
    top: 243px;
    display: flex;
    font-size: 13.5px;
    line-height: 18px;
    color: var(--ink);
  }
  .contacts__group { padding: 0 10px; border-left: 1.5px solid var(--ink); }
  .contacts__group:first-child { padding-left: 0; border-left: 0; }
  .contacts__line { display: flex; align-items: center; gap: 5px; white-space: nowrap; }
  .contacts__line svg { width: 10px; height: 10px; fill: var(--ink); flex: none; }

  .site {
    position: absolute;
    left: 0;
    right: 0;
    top: 194px;
    text-align: center;
    font-size: 13px;
    letter-spacing: 2px;
    color: var(--muted);
  }
</style>
</head>
<body>
  <section class="card card--front">
    <div class="brand"><span class="brand__mark"></span>KRL</div>

    <p class="holder">YOUR NAME, <span class="holder__title">Title</span></p>
    <div class="divider"></div>

    <div class="contacts">
      <div class="contacts__group">
        <p class="contacts__line">Street Name, City Name</p>
        <p class="contacts__line">State, City Zip 123 4560</p>
      </div>
      <div class="contacts__group">
        <p class="contacts__line">
          <svg viewBox="0 0 10 10" aria-hidden="true"><path d="M2 0.5 L4 2.5 L3 3.8 Q4.5 6 6.2 7 L7.5 6 L9.5 8 L8 9.5 Q3.5 9 0.5 2 Z"/></svg>123-456-7890
        </p>
        <p class="contacts__line">
          <svg viewBox="0 0 10 10" aria-hidden="true"><path d="M2 3 L3 1 H7 L8 3 H9.5 V7.5 H8.5 V9 H7 V7.5 H3 V9 H1.5 V7.5 H0.5 V3 Z"/></svg>123-456-7890
        </p>
      </div>
      <div class="contacts__group">
        <p class="contacts__line">
          <svg viewBox="0 0 10 10" aria-hidden="true"><path d="M0.5 2 H9.5 V8.5 H0.5 Z M1 2.5 L5 5.5 L9 2.5" stroke="#fff" stroke-width="0.8"/></svg>info@krl-example.com.sa
        </p>
        <p class="contacts__line">
          <svg viewBox="0 0 10 10" aria-hidden="true"><circle cx="5" cy="5" r="4.5"/><path d="M0.5 5 H9.5 M5 0.5 V9.5" stroke="#fff" stroke-width="0.7"/></svg>www.website.com
        </p>
      </div>
    </div>
  </section>

  <section class="card card--back">
    <div class="brand"><span class="brand__mark"></span>KRL</div>
    <p class="site">www.website.com</p>
  </section>
</body>
</html>
```